Talbrook Answering Service Brochure

Design a brochure for an answering service/call center based on the information submitted/attached. Photos and text will be included. Would like it designed to complement the logo provided. This brochure will explain to the potential customer who we are and what we have to offer.

The Talbrook representatives take and processes inbound calls, 24-7-365

Target Market(s)

Any business, however, primarily Medical, oil and gas, non profits, and the service industry

Industry/Entity Type

Telecommunications

Font styles to use
Serif
Other font styles liked:
• coordinate with logo

Requirements
Must have
• Modern, bright, bold and neatly structured brochure that will complement the logo and our brand.

```html
<!DOCTYPE html>
<html lang="en">
<head>
<meta charset="utf-8">
<title>Talbrook Answering Service – Brochure Inside Spread</title>
<link rel="stylesheet" href="https://fonts.googleapis.com/css2?family=Open+Sans:wght@400;600;700&family=Russo+One&family=Great+Vibes&display=swap">
<style>
  :root {
    --page-bg: #cfcccb;
    --paper: #ffffff;
    --paper-tint: #f7e9ea;
    --brand-red: #d7262f;
    --headline-red: #e0505a;
    --charcoal: #2f2b2d;
    --ink: #3b3738;
    --photo-warm: #d9cbc4;
    --photo-cool: #dfe2e6;
  }
  * { box-sizing: border-box; margin: 0; padding: 0; }
  html, body { width: 1200px; height: 1200px; overflow: hidden; }
  body {
    background: var(--page-bg);
    font-family: "Open Sans", Arial, sans-serif;
    color: var(--ink);
  }
  .brochure {
    position: absolute;
    left: 30px; top: 160px;
    width: 1140px; height: 880px;
    background: linear-gradient(135deg, var(--paper) 0%, var(--paper-tint) 45%, var(--paper) 100%);
    overflow: hidden;
    box-shadow: 0 6px 24px rgba(0,0,0,.18);
  }
  .swoosh { position: absolute; left: 0; width: 1140px; pointer-events: none; }
  .swoosh--top { top: 0; height: 120px; }
  .swoosh--bottom { bottom: 0; height: 150px; }
  .panel {
    position: absolute; top: 0; width: 380px; height: 880px;
    font-size: 12.5px; line-height: 1.55;
  }
  .panel + .panel { border-left: 1px solid rgba(0,0,0,.05); }
  .panel--left { left: 0; }
  .panel--middle { left: 380px; }
  .panel--right { left: 760px; }
  .photo {
    position: absolute;
  }
  .photo--agent-desk {
    left: 0; top: 0; width: 380px; height: 200px;
    background: linear-gradient(120deg, var(--photo-warm), var(--photo-cool));
  }
  .photo--agent-smile {
    left: 90px; bottom: 0; width: 290px; height: 440px;
    background: radial-gradient(ellipse at 60% 40%, #efe6e2 0%, #d8d4d6 55%, #c9ccd3 100%);
  }
  .copy { position: absolute; left: 34px; right: 30px; }
  .copy p { margin-bottom: 18px; }
  .years-badge {
    position: absolute; left: 268px; top: 188px;
    width: 92px; height: 92px; border-radius: 50%;
    background: var(--brand-red);
    color: #fff; text-align: center;
    font-family: "Great Vibes", cursive;
    display: flex; flex-direction: column; justify-content: center;
    line-height: .9;
  }
  .years-badge .num { font-size: 38px; }
  .years-badge .label { font-size: 24px; }
  .headline {
    font-family: "Russo One", sans-serif;
    font-weight: 400;
    color: var(--headline-red);
    font-variant: small-caps;
    font-size: 27px; line-height: 1.12;
    margin-bottom: 18px;
  }
  .subhead {
    font-weight: 700; font-size: 16px; color: var(--ink);
    margin-bottom: 10px;
  }
  .service-list { list-style: none; }
  .service-list li { position: relative; padding-left: 26px; }
  .service-list li::before {
    content: "•"; position: absolute; left: 4px; color: var(--ink);
  }
</style>
</head>
<body>
  <main class="brochure">
    <svg class="swoosh swoosh--top" viewBox="0 0 1140 120" preserveAspectRatio="none" aria-hidden="true">
      <path d="M380 0 H1140 V0 C1010 20 820 70 380 60 Z" fill="var(--charcoal)"/>
      <path d="M380 60 C820 70 1010 20 1140 0 L1140 8 C1010 30 820 78 380 68 Z" fill="var(--brand-red)"/>
    </svg>

    <section class="panel panel--left">
      <div class="photo photo--agent-desk" role="img" aria-label="Photo of a smiling call center agent wearing a headset at her desk"></div>
      <div class="years-badge"><span class="num">84</span><span class="label">years</span></div>
      <div class="copy" style="top:212px; right:120px;">
        <p>Talbrook, over the past 84 years, has operated through wars, floods and hurricanes. Our long history is important as it shows Consistency, Professionalism, Experience, and a Can Do Attitude, which is hard to find in the answering service industry today.</p>
      </div>
      <div class="copy" style="top:370px;">
        <p>At Talbrook, you'll never be just another a number. We will become part of YOUR team on day one and remain there, ready and honored to serve by providing reliable, professional answering services, 24-7-365, as needed.</p>
        <p>Talbrook Answering Service is your award winning, five start center, backed by critical redundancy and a solid infrastructure, for the highest availability possible.</p>
        <h2 class="headline">Automated or Live – Answering Services That Work For You</h2>
        <p>Tell us about your needs and your budget and we'll do the rest. Talbrook selects a system that satisfies your</p>
      </div>
    </section>

    <section class="panel panel--middle">
      <div class="copy" style="top:70px;">
        <p>basic requirements, then evaluates your business to find a long-term solution that will work for you and your customers.</p>
        <h2 class="headline">Still Growing? Find a Scalable Phone Answering Service</h2>
        <p>A scalable solution is one that doesn't waste resources when you don't need them, but easily adapts to future growth. All of our services at Talbrook grow with you, meaning you don't pay for additional support until you need it.</p>
        <h3 class="subhead">Live Answering Service</h3>
        <p>Steady Reply is more than an answering service, it's an extension of your company. Our professional representatives take pride in being your direct line of communication with existing customers, potential customers and valued business partners. Before we start fielding calls, our representatives are trained according to the details of your business and industry.</p>
        <ul class="service-list">
          <li>24 Hour Answering Service</li>
          <li>Virtual Receptionist / Virtual Assistant</li>
          <li>Live Message Relay</li>
          <li>Help Desk Overflow</li>
          <li>Call Screening</li>
          <li>Bilingual Answering (Spanish Answering Service)</li>
          <li>Automated Services</li>
        </ul>
      </div>
    </section>

    <section class="panel panel--right">
      <div class="copy" style="top:110px;">
        <h3 class="subhead">Automated Services</h3>
        <p>Live answering services are not necessary for all businesses. Steady Reply offers automated answering services as a cost-effective option for continuous customer contact. And just because it's "automated" that doesn't mean it isn't tailored to the specific needs of your business.</p>
        <p>(Live and automated services can be combined for very cost effective and professional solution.)</p>
      </div>
      <div class="photo photo--agent-smile" role="img" aria-label="Photo of a smiling customer service representative wearing a headset, colleague blurred behind"></div>
    </section>

    <svg class="swoosh swoosh--bottom" viewBox="0 0 1140 150" preserveAspectRatio="none" aria-hidden="true">
      <path d="M0 150 C60 70 300 40 760 40 L760 150 Z" fill="var(--charcoal)"/>
      <path d="M0 150 C50 60 300 28 760 30 L760 40 C300 40 60 70 0 150 Z" fill="var(--brand-red)"/>
    </svg>
  </main>
</body>
</html>
```